SOLVE Study flyer

I need help designing a flyer for a research study that will include brain imaging in adolescents. The info is in the attached document. The study is called the Sequoia Outlook Lantern Valley Echo (SOLVE) study. Ideally this would be returned as a document that I can edit in the future as we will have several new recruitment phases (different age groups, etc. I also would love to have a logo designed as part of this project, but I recognize that might be a separate design request.

```html
<!DOCTYPE html>
<html lang="en">
<head>
<meta charset="UTF-8">
<title>SOLVE Study Flyer</title>
<link rel="stylesheet" href="https://fonts.googleapis.com/css2?family=Oswald:wght@500;600;700&family=Poppins:wght@500;600&display=swap">
<style>
  :root {
    --blue: #0560bf;
    --ink: #111111;
    --black-band: #161616;
    --white: #ffffff;
    --backdrop: #9a9a9a;
    --photo-warm: #c9963f;
    --photo-green: #8fa35a;
  }
  * { margin: 0; padding: 0; box-sizing: border-box; }
  html, body { width: 888px; height: 1200px; overflow: hidden; background: var(--backdrop); }
  .flyer {
    position: absolute; left: 44px; top: 0;
    width: 800px; height: 1200px;
    background: var(--white); overflow: hidden;
    font-family: 'Poppins', sans-serif; color: var(--ink);
  }
  .hero-art { position: absolute; left: 0; top: 0; }
  .study-title {
    position: absolute; left: 34px; top: 26px;
    font-family: 'Oswald', sans-serif; font-weight: 600;
    font-size: 38px; line-height: 43px; color: var(--ink);
    letter-spacing: -0.3px;
  }
  .headline {
    position: absolute; left: 34px; top: 196px;
    white-space: nowrap;
    font-family: 'Oswald', sans-serif; font-weight: 600;
    font-size: 43px; line-height: 50px; color: var(--white);
    letter-spacing: -0.5px;
    text-shadow: 0 2px 4px rgba(0,0,0,0.25);
  }
  .intro {
    position: absolute; left: 32px; top: 456px; width: 455px;
    font-size: 15px; line-height: 23.5px; font-weight: 500; color: var(--white);
  }
  .section-heading {
    font-family: 'Oswald', sans-serif; font-weight: 600;
    font-size: 29px; line-height: 41px; color: var(--ink);
    letter-spacing: -0.3px;
  }
  .column { position: absolute; top: 604px; }
  .column--involves { left: 30px; width: 390px; }
  .column--involves .section-heading { margin-bottom: 22px; }
  .column--eligible { left: 436px; width: 350px; }
  .column--eligible .section-heading { margin-bottom: 16px; }
  .column--eligible .check-list { margin-left: 10px; }
  .check-list { list-style: none; }
  .check-list li {
    position: relative; padding-left: 31px; margin-bottom: 16px;
    font-size: 15px; line-height: 20px; font-weight: 500; white-space: nowrap;
  }
  .check-list li svg { position: absolute; left: 0; top: 1px; }
  .cta-band {
    position: absolute; left: 0; top: 1026px; width: 800px; height: 174px;
    background: var(--black-band);
  }
  .cta-box {
    position: absolute; left: 65px; top: 900px; width: 670px; height: 154px;
    background: var(--blue); border-radius: 30px;
    text-align: center; color: var(--white);
    font-family: 'Oswald', sans-serif; font-weight: 600;
  }
  .cta-box__main { font-size: 50px; line-height: 60px; padding-top: 20px; }
  .cta-box__sub { font-size: 36px; line-height: 46px; }
  .contact-email {
    position: absolute; left: 0; top: 1050px; width: 800px;
    text-align: center; color: var(--white);
    font-size: 35px; line-height: 48px; font-weight: 500;
  }
  .contact-email svg { vertical-align: middle; margin-right: 16px; margin-top: -4px; }
  .compensation {
    position: absolute; left: 101px; top: 1116px; width: 598px; height: 66px;
    background: var(--white); border-radius: 24px;
    text-align: center; color: var(--blue);
    font-family: 'Oswald', sans-serif; font-weight: 700;
    font-size: 48px; line-height: 64px;
  }
</style>
</head>
<body>
<main class="flyer">
  <svg class="hero-art" width="800" height="590" viewBox="0 0 800 590">
    <defs>
      <linearGradient id="photoTone" x1="0" y1="0" x2="1" y2="1">
        <stop offset="0" stop-color="#b9b3a6"/>
        <stop offset="0.45" stop-color="var(--photo-green)"/>
        <stop offset="0.75" stop-color="var(--photo-warm)"/>
        <stop offset="1" stop-color="#3a3030"/>
      </linearGradient>
    </defs>
    <path class="accent" d="M482 110 C505 60 535 25 572 0 H800 V110 Z" fill="var(--blue)"/>
    <path class="accent-line" d="M525 112 C540 70 558 32 584 -2" stroke="var(--white)" stroke-width="5" fill="none"/>
    <path class="photo" d="M307 110 H800 V513 H540 L269 168 Z" fill="url(#photoTone)" role="img" aria-label="Photo of three teenage girls in sweaters sitting outdoors looking at a tablet"/>
    <path class="panel" d="M0 175 H266 C340 175 385 200 410 250 C455 340 500 450 560 513 H748 C722 545 692 562 655 568 L640 575 H0 Z" fill="var(--blue)"/>
    <path class="panel-edge" d="M268 171 C343 171 389 197 415 248 C460 338 505 446 565 509 C602 549 632 566 668 572" stroke="var(--white)" stroke-width="6" fill="none"/>
  </svg>

  <h1 class="study-title">Sequoia Outlook<br>Lantern Valley<br>Echo</h1>

  <h2 class="headline">Are you the<br>parent of a child age<br>10-17 ? Do they worry<br>or overthink negative<br>emotions ?</h2>

  <p class="intro">Northfield University researchers are seeking girls age 10-17 for a study about brain activity in emotions and decision-making and how they relate to puberty, anxiety and depression.</p>

  <section class="column column--involves">
    <h3 class="section-heading">Study Participation Involves:</h3>
    <ul class="check-list">
      <li><svg width="18" height="18" viewBox="0 0 18 18"><circle cx="9" cy="9" r="9" fill="var(--blue)"/><path d="M5 9.3 L8 12 L13 6.5" stroke="#fff" stroke-width="2" fill="none"/></svg>One one-hour interview<br>(online or in-person) where your child<br>will discuss their thoughts</li>
      <li><svg width="18" height="18" viewBox="0 0 18 18"><circle cx="9" cy="9" r="9" fill="var(--blue)"/><path d="M5 9.3 L8 12 L13 6.5" stroke="#fff" stroke-width="2" fill="none"/></svg>Online questionnaires (parent and child)</li>
      <li><svg width="18" height="18" viewBox="0 0 18 18"><circle cx="9" cy="9" r="9" fill="var(--blue)"/><path d="M5 9.3 L8 12 L13 6.5" stroke="#fff" stroke-width="2" fill="none"/></svg>One two-hour visit where your child will<br>complete an MRI scan, answer questions<br>about their puberty stage, and have a<br>small hair sample taken to study<br>puberty hormones</li>
    </ul>
  </section>

  <section class="column column--eligible">
    <h3 class="section-heading">Your Child may be<br>Eligible if they:</h3>
    <ul class="check-list">
      <li><svg width="18" height="18" viewBox="0 0 18 18"><circle cx="9" cy="9" r="9" fill="var(--blue)"/><path d="M5 9.3 L8 12 L13 6.5" stroke="#fff" stroke-width="2" fill="none"/></svg>Are age 10-17</li>
      <li><svg width="18" height="18" viewBox="0 0 18 18"><circle cx="9" cy="9" r="9" fill="var(--blue)"/><path d="M5 9.3 L8 12 L13 6.5" stroke="#fff" stroke-width="2" fill="none"/></svg>Tend to worry or overthink negative<br>thoughts</li>
      <li><svg width="18" height="18" viewBox="0 0 18 18"><circle cx="9" cy="9" r="9" fill="var(--blue)"/><path d="M5 9.3 L8 12 L13 6.5" stroke="#fff" stroke-width="2" fill="none"/></svg>Have not been diagnosed with<br>psychosis, learning problems, or<br>autism</li>
    </ul>
  </section>

  <div class="cta-band"></div>
  <div class="cta-box">
    <p class="cta-box__main">Interested in participating?</p>
    <p class="cta-box__sub">Want more information? Please contact us!</p>
  </div>

  <p class="contact-email"><svg width="22" height="15" viewBox="0 0 22 15"><rect width="22" height="15" fill="var(--blue)"/><path d="M0 0 L11 8 L22 0 M0 15 L8 6.5 M22 15 L14 6.5" stroke="var(--black-band)" stroke-width="1.5" fill="none"/></svg>solvestudy@northfield.edu</p>

  <div class="compensation">Compensation up to $140</div>
</main>
</body>
</html>
```